Ridgeline Haul Carriers - Website

A clean, not cluttered informative website for our business. We specialize in the transportation of radioactive materials across North America. The site is mostly for information about our company and will not be used to attract business but will be used to attract employee's mainly drivers. Driver's are very hard to find in our area. One of the pages needs to be a job's posting page with an apply now button. Either an application can be filled out there or a resume can be uploaded which ever functionality works better. I would like a website that I can easily edit, ability to change text and photos.

Number of Pages Required

5+ page

Colors

Designer to choose colors to be used in the design.

Requirements
Must have
• Home - About - Services - Jobs - Contact pages
• A way prospective employee's can apply or upload their resume to be emailed to me
• Very clean apperance
Should not have
• I don't want it to be busy

```html
<!DOCTYPE html>
<html lang="en">
<head>
<meta charset="utf-8">
<title>Ridgeline Haul Carriers – About Us</title>
<link rel="stylesheet" href="https://fonts.googleapis.com/css2?family=Archivo+Black&family=Montserrat:ital,wght@0,400;0,500;0,600;0,700;1,400&display=swap">
<style>
  :root {
    --navy: #14213d;
    --navy-deep: #0d1529;
    --orange: #f08a12;
    --ink: #111520;
    --muted: #9a9ea8;
    --body: #444a55;
    --paper: #f7f7f7;
    --photo-dark: #2a2620;
    --photo-gold: #8a6a28;
  }
  * { box-sizing: border-box; margin: 0; padding: 0; }
  html, body { width: 1200px; height: 965px; overflow: hidden; background: var(--paper); }
  body { font-family: "Montserrat", sans-serif; color: var(--ink); position: relative; }

  .site-header { position: absolute; top: 0; left: 0; width: 1200px; height: 230px; }
  .header-band {
    position: absolute; top: 0; left: 0; width: 760px; height: 200px;
    background: linear-gradient(135deg, var(--navy) 0%, var(--navy-deep) 100%);
  }
  .header-photo {
    position: absolute; top: 0; left: 760px; width: 440px; height: 230px;
    background: linear-gradient(180deg, var(--photo-dark) 0%, #3b3326 60%, var(--photo-gold) 100%);
  }
  .main-nav { position: absolute; left: 200px; top: 150px; display: flex; gap: 44px; }
  .main-nav a {
    color: #fff; text-decoration: none; font-size: 14px; font-weight: 600; letter-spacing: .5px;
  }

  .page-title {
    position: absolute; left: 110px; top: 250px;
    font-family: "Archivo Black", sans-serif; font-size: 50px; letter-spacing: 1px;
  }

  .topic-list { list-style: none; }
  .topic-list li { position: absolute; font-size: 19px; line-height: 1.1; width: 200px; }
  .topic-list .topic { color: var(--muted); font-style: italic; left: 110px; }
  .topic-list .topic-active { color: var(--ink); font-weight: 600; left: 170px; }

  .brand {
    position: absolute; left: 780px; top: 290px;
    display: flex; align-items: center; gap: 12px;
  }
  .brand-mark { width: 18px; height: 18px; border-radius: 50%; background: var(--orange); }
  .brand-name { font-weight: 700; font-size: 27px; color: var(--orange); }

  .feature-photo {
    position: absolute; left: 560px; top: 370px; width: 580px; height: 290px;
    background: linear-gradient(180deg, #9ca0a8 0%, #6d7075 55%, #4a4b4e 100%);
  }
  .feature-title {
    position: absolute; left: 560px; top: 700px;
    font-size: 21px; font-weight: 500; letter-spacing: 1px; text-transform: uppercase;
  }
  .page-count {
    position: absolute; left: 1090px; top: 742px;
    font-size: 10px; font-weight: 600; color: var(--ink); text-transform: uppercase; letter-spacing: .5px;
  }
  .feature-text {
    position: absolute; left: 560px; top: 765px; width: 460px;
    font-size: 12px; line-height: 1.5; color: var(--body);
  }
  .apply-button {
    position: absolute; left: 920px; top: 895px; width: 180px; height: 46px;
    display: flex; align-items: center; justify-content: center;
    background: var(--orange); color: #fff; text-decoration: none;
    font-size: 14px; font-weight: 700; letter-spacing: 1px; text-transform: uppercase;
  }
</style>
</head>
<body>
  <header class="site-header">
    <div class="header-band"></div>
    <div class="header-photo" role="img" aria-label="Header photograph in dark and warm gold tones"></div>
    <nav class="main-nav">
      <a href="#">HOME</a>
      <a href="#">ABOUT US</a>
      <a href="#">SERVICES</a>
      <a href="#">JOBS</a>
      <a href="#">CONTACT US</a>
    </nav>
  </header>

  <main>
    <h1 class="page-title">ABOUT US</h1>

    <ul class="topic-list">
      <li class="topic" style="top:340px">Our story</li>
      <li class="topic-active" style="top:500px">Our drivers</li>
      <li class="topic" style="top:640px">Safety first</li>
      <li class="topic" style="top:770px">Our fleet</li>
    </ul>

    <div class="brand">
      <span class="brand-mark"></span>
      <span class="brand-name">Ridgeline Haul Carriers</span>
    </div>

    <div class="feature-photo" role="img" aria-label="Photograph of a grey semi truck hauling a flatbed of cylindrical containers"></div>

    <h2 class="feature-title">Our drivers</h2>
    <span class="page-count">Page 2</span>
    <p class="feature-text">Our drivers move sensitive cargo with care across the continent, backed by steady routes, fair pay and a team that values safety above all.</p>

    <a class="apply-button" href="#">Apply now</a>
  </main>
</body>
</html>
```